Heritage Hollow Business Cards

Require a business card design. <br/><br/>Needs to include logo (either round or long version) plus these details:<br/>Maya Torvell<br/>Heritage Hollow<br/>maya@kelvadtrading.com.au<br/>02 6481 7395<br/>PO Box Glenwarra NSW 2791<br/>www.heritagehollow.com.au<br/><br/>I need in an editable format so that I can create for multiple staff members. <br/><br/>

Target Market(s)

We are an online store selling renovation products to home owners are builders. Looking for a classic classy design.

Industry/Entity Type

Home And Garden

Contact Information for Business Card

Maya Torvell
Heritage Hollow
maya@kelvadtrading.com.au
02 6481 7395
PO Box Glenwarra NSW 2791
www.heritagehollow.com.au

Colors

Designer to choose colors to be used in the design.

Requirements
Must have
• Must include Logo.

```html
<!DOCTYPE html>
<html lang="en">
<head>
<meta charset="utf-8">
<title>Heritage Hollow Business Cards</title>
<link rel="stylesheet" href="https://fonts.googleapis.com/css2?family=Della+Respira&family=Poppins:wght@400;500;600&display=swap">
<style>
  :root {
    --backdrop: #3b3937;
    --card-green: #587766;
    --ink-green: #3f5e4f;
    --ink-dark: #2b2b2b;
    --paper: #ffffff;
    --chalk: #f1efe6;
    --serif: "Della Respira", Georgia, serif;
    --sans: "Poppins", Arial, sans-serif;
  }
  * { margin: 0; padding: 0; box-sizing: border-box; }
  html, body { width: 1200px; height: 900px; overflow: hidden; }
  body { background: var(--backdrop); position: relative; font-family: var(--sans); }

  .card {
    position: absolute;
    left: 311px;
    width: 577px;
    height: 328px;
  }

  /* Front */
  .card-front { top: 98px; background: var(--card-green); }
  .front-name {
    position: absolute;
    left: 0; right: 0; top: 232px;
    text-align: center;
    font-family: var(--serif);
    font-size: 40px;
    color: var(--chalk);
    letter-spacing: 0.3px;
  }
  .front-web-row {
    position: absolute;
    left: 20px; right: 22px; top: 277px;
    display: flex;
    align-items: center;
    gap: 10px;
  }
  .front-web-row .rule { flex: 1; height: 1.5px; background: var(--chalk); }
  .front-web {
    font-size: 14px;
    color: var(--chalk);
    letter-spacing: 0.2px;
  }

  /* Back */
  .card-back { top: 472px; background: var(--paper); }
  .brand-badge {
    position: absolute;
    left: 59px; top: 85px;
    width: 158px; height: 158px;
    border: 1.5px solid var(--ink-dark);
    border-radius: 50%;
    display: flex;
    align-items: center;
    justify-content: center;
    text-align: center;
  }
  .brand-badge .brand-name {
    font-family: var(--serif);
    font-size: 25px;
    line-height: 1.05;
    color: var(--ink-dark);
  }
  .divider {
    position: absolute;
    left: 261px; top: 80px;
    width: 1.5px; height: 168px;
    background: var(--ink-dark);
  }
  .contact {
    position: absolute;
    left: 289px; top: 77px;
  }
  .contact .person {
    font-size: 16px;
    font-weight: 600;
    color: var(--ink-green);
    line-height: 1.2;
  }
  .contact .company {
    font-size: 14px;
    color: var(--ink-dark);
    line-height: 1.3;
  }
  .contact .address {
    margin-top: 12px;
    font-size: 15px;
    color: var(--ink-green);
    line-height: 1.35;
  }
  .contact .lines { margin-top: 11px; list-style: none; }
  .contact .lines li {
    display: flex;
    align-items: center;
    gap: 8px;
    font-size: 15px;
    color: var(--ink-dark);
    height: 26.5px;
  }
  .contact .icon { width: 18px; height: 18px; flex: none; }
  .contact .icon path, .contact .icon circle, .contact .icon rect { fill: var(--ink-green); }
</style>
</head>
<body>

<section class="card card-front" aria-label="Business card front">
  <div class="front-name">Heritage Hollow</div>
  <div class="front-web-row">
    <span class="rule"></span>
    <span class="front-web">www.heritagehollow.com.au</span>
    <span class="rule"></span>
  </div>
</section>

<section class="card card-back" aria-label="Business card back">
  <div class="brand-badge">
    <span class="brand-name">Heritage<br>Hollow</span>
  </div>
  <div class="divider"></div>
  <div class="contact">
    <div class="person">Maya Torvell</div>
    <div class="company">Heritage Hollow</div>
    <div class="address">PO Box<br>Glenwarra NSW 2791</div>
    <ul class="lines">
      <li>
        <svg class="icon" viewBox="0 0 24 24" aria-hidden="true"><path d="M6.6 10.8a15.2 15.2 0 0 0 6.6 6.6l2.2-2.2c.3-.3.7-.4 1-.2 1.1.4 2.3.6 3.6.6.6 0 1 .4 1 1V20c0 .6-.4 1-1 1A17 17 0 0 1 3 4c0-.6.4-1 1-1h3.5c.6 0 1 .4 1 1 0 1.3.2 2.5.6 3.6.1.3 0 .7-.2 1l-2.3 2.2z"/></svg>
        <span>02 6481 7395</span>
      </li>
      <li>
        <svg class="icon" viewBox="0 0 24 24" aria-hidden="true"><path d="M3 5h18c.6 0 1 .4 1 1v.6l-10 6.2L2 6.6V6c0-.6.4-1 1-1zm-1 3.9 10 6.2 10-6.2V18c0 .6-.4 1-1 1H3c-.6 0-1-.4-1-1V8.9z"/></svg>
        <span>maya@kelvadtrading.com.au</span>
      </li>
      <li>
        <svg class="icon" viewBox="0 0 24 24" aria-hidden="true"><path d="M12 2a10 10 0 1 0 0 20 10 10 0 0 0 0-20zm-1 17.9A8 8 0 0 1 4.2 10L9 14.8v1c0 1.1.9 2 2 2v2.1zm6.9-2.5c-.3-.8-1-1.4-1.9-1.4h-1v-3c0-.6-.4-1-1-1H8v-2h2c.6 0 1-.4 1-1V7h2c1.1 0 2-.9 2-2v-.4a8 8 0 0 1 2.9 12.8z"/></svg>
        <span>www.heritagehollow.com.au</span>
      </li>
    </ul>
  </div>
</section>

</body>
</html>
```